Web Design Project

We are looking for a unified design of Corporate Website, Stationary (Including Letterhead and Envelopes), Business Cards, Email Footers and Sales & Marketing Brochures.

Color palette should include:
Black (R: 24, G:24, B:24)
Red (R:206, G:0, B:39)
Dark Grey (R:51, G:51, B:51)
Light Grey/Silver (R:203, G:203, B:203)

As we do business in North America and the UK, designs should be reflective of standard sizing for both regions.

Check out our website to better understand who we are: www.KLVR.com and a copy of our Logo has been uploaded for reference.
Updates

Hello all, we had not anticipated the volume of unique, high quality designs we have received, thank you all for your submissions. A team review of all designs will take place the week of December 8th, and final decisions and selections made. Thank you again

Target Market(s)

Automotive Parts Wholesalers, Vehicle Repair Specialists, Automotive Parts Manufacturers, Automotive Insurance

Industry/Entity Type

Business

Font styles to use
Sans Serif

Requirements
Must have
• - Color palette should include:
- Black (R: 24, G:24, B:24)
- Red (R:206, G:0, B:39)
- Dark Grey (R:51, G:51, B:51)
- Light Grey/Silver (R:203, G:203, B:203)
Should not have
• No Animations

```html
<!DOCTYPE html>
<html lang="en">
<head>
<meta charset="utf-8">
<title>Kelver Parts Solutions</title>
<link href="https://fonts.googleapis.com/css2?family=Oswald:wght@400;500&family=Roboto:wght@300;400&display=swap" rel="stylesheet">
<style>
:root{
  --black:#181818;
  --ink:#000;
  --red:#ce0027;
  --red-bright:#e8103f;
  --dark-grey:#333;
  --silver:#cbcbcb;
  --text-light:#bdbdbd;
  --body-text:#333;
  --strip-text:#5a5a5a;
}
*{margin:0;padding:0;box-sizing:border-box}
html,body{width:1200px;height:1044px;overflow:hidden;background:var(--black);font-family:'Roboto',sans-serif}
.page{position:relative;width:1200px;height:1044px;background:var(--black)}

.topbar{position:absolute;left:0;top:0;width:1200px;height:57px;background:linear-gradient(#2a2a2a,#1a1a1a);border-bottom:1px solid #333}
.nav{position:absolute;left:179px;top:12px;width:842px;display:flex;justify-content:space-between;align-items:center}
.nav a{color:#fff;text-decoration:none;font-size:12.5px;text-transform:uppercase;padding:10px 0;border-radius:4px}
.nav a.active{background:linear-gradient(var(--red-bright),#b8002a);padding:10px 12px}

.hero{position:absolute;left:0;top:57px;width:1200px;height:450px;background:linear-gradient(var(--ink) 0,var(--ink) 286px,#1e0208 300px,#0f0104 450px)}
.brand{position:absolute;left:180px;top:90px;display:flex;align-items:center;gap:9px}
.brand-mark{width:46px;height:46px;border-radius:50%;background:#9a9a9a}
.brand-name{color:#fff;font-size:21px;font-weight:400;letter-spacing:.5px}
.hero-title{position:absolute;left:176px;top:148px;width:300px;text-align:center;font-family:'Oswald',sans-serif;font-weight:500;font-size:35px;line-height:42px;color:var(--red);letter-spacing:-1px}
.hero-photo{position:absolute;left:500px;top:80px;width:540px;height:260px;background:radial-gradient(ellipse 50% 50% at 52% 55%,#8e8e8e 0,#5a5a5a 35%,#2a2a2a 62%,rgba(0,0,0,0) 100%)}
.dots{position:absolute;left:578px;top:327px;display:flex;gap:8px}
.dots span{width:9px;height:9px;border-radius:50%;background:#555}
.dots span.on{background:var(--red)}

.features{position:absolute;left:181px;top:407px;width:840px;height:245px;border:1px solid #999;border-radius:3px;background:linear-gradient(#f5f5f5,#eaeaea 45%,#a8a8a8);display:flex}
.feature{flex:1;text-align:center;padding-top:32px;position:relative}
.feature+.feature::before{content:"";position:absolute;left:0;top:40px;height:160px;width:1px;background:linear-gradient(transparent,#c8c8c8,transparent)}
.feature-icon{width:66px;height:66px;margin:0 auto;border-radius:50%;background:radial-gradient(circle at 40% 35%,#5a5a5a,#1e1e1e 70%);position:relative}
.feature-icon::after{content:"";position:absolute;right:-4px;bottom:2px;width:22px;height:22px;background:var(--red);transform:rotate(45deg);border-radius:3px}
.feature h3{margin-top:18px;font-family:'Oswald',sans-serif;font-weight:400;font-size:19px;color:var(--red);letter-spacing:-.4px}
.feature p{margin-top:8px;font-size:12.4px;line-height:20.5px;color:var(--body-text);padding:0 24px}

.welcome{position:absolute;left:180px;top:672px;width:548px}
.welcome h2{font-family:'Oswald',sans-serif;font-weight:400;font-size:23px;color:var(--red);letter-spacing:-.5px}
.welcome p{margin-top:2px;font-size:12.3px;line-height:25.7px;color:#a0a0a0}

.quote{position:absolute;left:757px;top:670px;width:263px;height:154px;background:#0f0f0f;padding:15px 12px 0 21px;font-size:11px;line-height:20.6px;color:var(--text-light)}
.quote a{color:var(--red);text-decoration:none}
.quote-tail{position:absolute;left:932px;top:823px}
.quote-author{position:absolute;left:753px;top:844px;font-size:12.5px;color:var(--text-light);text-transform:uppercase}

.makes{position:absolute;left:0;top:895px;width:1200px;height:82px;background:linear-gradient(#fafafa,#e4e4e4 60%,#c4c4c4);border-top:1px solid #bbb;border-bottom:1px solid #888}
.makes-row{position:absolute;left:181px;top:0;width:840px;height:82px;display:flex;justify-content:space-between;align-items:center}
.make{font-family:'Oswald',sans-serif;font-weight:400;font-size:13px;letter-spacing:.5px;text-transform:uppercase;color:var(--strip-text)}

.footer-copy{position:absolute;left:180px;top:1004px;font-size:11.5px;color:#999}
.social{position:absolute;left:879px;top:997px;display:flex;gap:5px}
.social span{width:24px;height:24px;border-radius:4px;background:linear-gradient(#e0e0e0,#9a9a9a);box-shadow:inset 0 0 0 1px #777}
</style>
</head>
<body>
<div class="page">
  <header class="topbar">
    <nav class="nav">
      <a class="active" href="#">Home</a>
      <a href="#">Intelligent Sales &amp; Marketing</a>
      <a href="#">Kelver Awards</a>
      <a href="#">References</a>
      <a href="#">Careers</a>
      <a href="#">About Us</a>
      <a href="#">Contact Us</a>
    </nav>
  </header>

  <section class="hero">
    <div class="brand"><span class="brand-mark"></span><span class="brand-name">Kelver Parts Solutions</span></div>
    <h1 class="hero-title">GENUINE PARTS SALES &amp;<br>MARKETING</h1>
    <div class="hero-photo" role="img" aria-label="Silver convertible sports car"></div>
    <div class="dots"><span></span><span class="on"></span><span></span></div>
  </section>

  <section class="features">
    <div class="feature">
      <div class="feature-icon" role="img" aria-label="Steering wheel icon"></div>
      <h3>AUTOMOTIVE PARTS WHOLESALERS</h3>
      <p>Ut wisi enim ad minim veniam, quis nostr ud exerci tation ullamcorper suscipit lobortis nisl ut aliquip.</p>
    </div>
    <div class="feature">
      <div class="feature-icon" role="img" aria-label="Gear and piston icon"></div>
      <h3>VEHICLE REPAIR SPECIALISTS</h3>
      <p>Ut wisi enim ad minim veniam, quis nostr ud exerci tation ullamcorper suscipit lobortis nisl ut aliquip.</p>
    </div>
    <div class="feature">
      <div class="feature-icon" role="img" aria-label="Wheel and tyre icon"></div>
      <h3>AUTOMOTIVE PARTS MANUFACTURERS</h3>
      <p>Ut wisi enim ad minim veniam, quis nostr ud exerci tation ullamcorper suscipit lobortis nisl ut aliquip.</p>
    </div>
  </section>

  <section class="welcome">
    <h2>WELCOME TO KELVER</h2>
    <p>Lorem ipsum dolor sit amet, consectetuer adipiscing elit, sed diam nonummy nibh euismod tincidunt ut laoreet dolore magna aliquam erat volutpat. Ut wisi enim ad minim veniam, quis nostrud exerci tation ullamcorper suscipit lobortis nisl ut aliquip ex ea commodo consequat. Duis autem vel eum iriure dolor in hendrerit in vulputate velit esse molestie consequat, vel illum dolore eu feugiat nulla facilisis at vero eros et accumsan et iusto odio dignissim qui blandit praesent luptatum zzril delenit augue duis dolore te feugait nulla facilisi.</p>
  </section>

  <aside class="quote">
    Bluejay MotorsWe would not, and do not, hesitate to recommend your company to any motor company seeking cost effective parts representation of the highest standard.I am sure that you are aware that we have used your company for many years... <a href="#">READ MORE</a>
  </aside>
  <svg class="quote-tail" width="88" height="30" viewBox="0 0 88 30"><polygon points="88,0 60,0 0,30 40,0" fill="#0f0f0f"/></svg>
  <div class="quote-author">Dale Morton, Parts Manager</div>

  <section class="makes" aria-label="Vehicle makes served">
    <div class="makes-row">
      <span class="make">Arden</span><span class="make">Belvo</span><span class="make">Corra</span><span class="make">Dravo</span>
      <span class="make">Elmar</span><span class="make">Fenix</span><span class="make">Garo</span><span class="make">Halden</span>
      <span class="make">Ivra</span><span class="make">Jorvik</span><span class="make">Kessa</span><span class="make">Lunor</span>
      <span class="make">Marno</span><span class="make">Novo</span>
    </div>
  </section>

  <footer>
    <p class="footer-copy">Copyrights@2014Kelver Parts Solutions. All Right Reserved.</p>
    <div class="social"><span></span><span></span><span></span><span></span><span></span></div>
  </footer>
</div>
</body>
</html>
```